Website Revamp: Bravoly.com

Just got a new logo looking for a web design to go with the business. I need the photoshop files and stock photos. No Word Press Please.

```html
<!DOCTYPE html>
<html lang="en">
<head>
<meta charset="utf-8">
<title>Bravoly Auto Recycling</title>
<link href="https://fonts.googleapis.com/css2?family=Poppins:wght@400;500;600;700&family=Open+Sans:wght@400;600;700&display=swap" rel="stylesheet">
<style>
:root{
  --green:#6cbb3c;
  --green-dark:#5aa62c;
  --ink:#1b1b1b;
  --text:#333;
  --muted:#555;
  --light:#f2f0f0;
  --slate:#6c777a;
  --footer:#6b7477;
  --white:#fff;
}
*{box-sizing:border-box;margin:0;padding:0}
html,body{width:1200px;height:4454px;overflow:hidden}
body{position:relative;font-family:"Open Sans",sans-serif;color:var(--text);background:var(--white)}
.abs{position:absolute}
.heading{font-family:"Poppins",sans-serif;font-weight:600;color:var(--ink);text-align:center;font-size:24px;letter-spacing:.3px}
.rule{width:52px;height:3px;background:#8a8a8a;margin:14px auto 0}
.btn{display:inline-block;background:var(--green);color:var(--white);font-family:"Poppins",sans-serif;font-weight:600;text-align:center;letter-spacing:.4px}
.btn-sm{font-size:10px;padding:6px 10px}

/* hero */
.hero{left:0;top:0;width:1200px;height:640px;background:linear-gradient(180deg,#1f47b5 0%,#3b6fd6 30%,#7fa0cf 48%,#5c5a55 62%,#2c2a27 100%)}
.brand{left:133px;top:18px;width:170px;text-align:center}
.brand-dot{width:90px;height:90px;border-radius:50%;background:var(--green);margin:0 auto 8px}
.brand-name{font-family:"Poppins",sans-serif;font-weight:700;font-size:28px;color:var(--green);letter-spacing:1px}
.contact-top{top:22px;color:var(--white);font-size:14px}
.contact-top small{display:block;font-size:10px;font-weight:600;letter-spacing:.4px}
.contact-top .phone{color:#8fe04e;font-family:"Poppins",sans-serif;font-weight:600;font-size:19px}
.sep{top:24px;width:2px;height:34px;background:var(--white)}
.nav{left:510px;top:78px;display:flex;gap:24px;font-family:"Poppins",sans-serif;font-weight:600;font-size:13px;color:var(--white)}
.nav .active{color:#8fe04e}
.hero-title{left:301px;top:206px;font-family:"Poppins",sans-serif;font-weight:700;font-size:38px;color:var(--white)}
.hero-sub{left:301px;top:254px;font-family:"Poppins",sans-serif;font-weight:600;font-size:17px;color:var(--white)}
.hero-btn{left:301px;top:297px;width:119px;height:37px;line-height:37px;font-size:14px}

/* process */
.process-title{left:0;top:690px;width:1200px}
.step{top:796px;width:320px;text-align:center}
.step .icon{height:84px;display:flex;flex-direction:column;align-items:center;justify-content:flex-end}
.step h3{font-family:"Poppins",sans-serif;font-weight:600;font-size:15px;line-height:20px;color:var(--ink);margin:14px 0 40px}
.step p{font-size:12px;line-height:16px;color:var(--muted);padding:0 28px}
.step svg{display:block}
.step .line{width:46px;height:2px;background:var(--green);margin-top:6px}

/* why */
.why{left:0;top:1055px;width:1200px;height:498px;background:linear-gradient(90deg,#5fae32,#74c043 50%,#66b53a);clip-path:polygon(0 0,104px 48px,100% 48px,100% 100%,1090px 453px,0 453px)}
.why-mark{left:133px;top:1190px;width:232px;height:232px;border-radius:50%;background:var(--white);display:flex;align-items:center;justify-content:center;font-family:"Poppins",sans-serif;font-weight:700;font-size:30px;color:var(--green)}
.why-divider{left:430px;top:1162px;width:2px;height:287px;background:rgba(255,255,255,.6)}
.why-title{left:514px;top:1152px;font-family:"Poppins",sans-serif;font-weight:600;font-size:28px;color:var(--white)}
.why-list{top:1234px;list-style:none;color:var(--white);font-size:16px;font-weight:600}
.why-list li{height:29px;display:flex;align-items:center;gap:10px}
.why-btn{left:522px;top:1411px;width:113px;height:33px;line-height:33px;background:var(--white);color:var(--green);font-size:14px}

/* services */
.services{left:0;top:1508px;width:1200px;height:498px;background:var(--light);clip-path:polygon(0 0,1090px 0,100% 45px,100% 100%,0 100%)}
.services-title{left:0;top:1548px;width:1200px}
.card{top:1632px;width:296px;height:324px;background:var(--white);box-shadow:0 2px 8px rgba(0,0,0,.08);text-align:center;padding-top:44px}
.card svg{display:block;margin:0 auto}
.card h3{font-family:"Poppins",sans-serif;font-weight:600;font-size:14px;color:var(--ink);margin:32px 0 12px}
.card p{font-size:11.5px;line-height:16px;color:var(--muted);padding:0 30px}
.card .btn{margin-top:20px}

/* testimonials */
.testimonials{left:0;top:2006px;width:1200px;height:484px;background:linear-gradient(180deg,#7b8588,#6a7477 60%,#5e6769)}
.t-title{left:0;top:2058px;width:1200px;color:var(--white)}
.t-title .rule{background:var(--white)}
.quote{left:251px;top:2150px;width:698px;text-align:center;color:var(--white);font-size:19px;line-height:25px}
.qmark{font-family:"Poppins",sans-serif;font-size:30px;font-weight:700;color:var(--white)}
.avatar{border-radius:50%;background:#b9b2aa;border:3px solid #d8d8d8}
.t-name{left:0;top:2420px;width:1218px;text-align:center;color:var(--white);font-size:11px;font-weight:700;letter-spacing:.5px}

/* blog */
.blog-title{left:0;top:2535px;width:1200px}
.post{top:2632px;width:221px;height:356px;border:1px solid #cfcfcf;background:var(--white)}
.post .photo{height:166px}
.post h4{font-family:"Poppins",sans-serif;font-weight:600;font-size:12.5px;line-height:17px;color:var(--ink);padding:24px 22px 10px}
.post p{font-size:10.5px;line-height:14px;color:var(--muted);padding:0 22px}
.post .btn{margin:14px 0 0 22px;font-size:9.5px;padding:5px 10px}

/* quality */
.quality{left:0;top:3052px;width:1200px;height:418px;background:var(--light)}
.quality-photo{left:0;top:3052px;width:591px;height:418px;background:linear-gradient(180deg,#8a8d8f,#5b5250 55%,#3c3633)}
.q-title{left:647px;top:3117px;font-family:"Poppins",sans-serif;font-weight:600;font-size:24px;color:var(--ink)}
.q-text{left:647px;top:3201px;width:410px;font-size:15px;line-height:22.5px;color:var(--text)}
.q-btn{left:647px;top:3370px;width:120px;height:35px;line-height:35px;font-size:15px}

/* call back */
.callback{left:0;top:3470px;width:1200px;height:576px;background:linear-gradient(180deg,#f4f4f4,#e6e7e8 60%,#d9dadb)}
.cb-title{left:0;top:3530px;width:1200px}
.form{left:277px;top:3627px;width:646px;height:367px;background:var(--white);box-shadow:0 2px 10px rgba(0,0,0,.06)}
.field{border:1px solid #9a9a9a;font-size:11px;color:#333;padding:0 16px;display:flex;align-items:center}
.field.msg{align-items:flex-start;padding-top:12px}
.submit{left:552px;top:3928px;width:95px;height:35px;line-height:35px;font-size:14px}

/* footer */
.footer{left:0;top:4046px;width:1200px;height:408px;background:var(--footer);color:var(--white)}
.f-mark{left:177px;top:4120px;width:134px;height:134px;border-radius:50%;border:6px solid var(--white)}
.f-name{left:130px;top:4262px;width:230px;text-align:center;font-family:"Poppins",sans-serif;font-weight:700;font-size:32px;color:var(--white);letter-spacing:1px}
.f-head{top:4112px;font-family:"Poppins",sans-serif;font-weight:600;font-size:14px;color:var(--white)}
.f-menu{left:441px;top:4150px;list-style:none;font-size:11.5px;line-height:26px}
.f-row{display:flex;gap:14px;align-items:flex-start;font-size:13px;line-height:18px}
.f-ico{flex:none;width:24px;height:24px;border-radius:50%;background:var(--white);display:flex;align-items:center;justify-content:center;margin-top:4px}
.copy{left:0;top:4408px;width:1200px;text-align:center;font-size:11px}
</style>
</head>
<body>

<!-- Hero -->
<div class="abs hero" role="img" aria-label="Scrapyard with a crane lifting a pickup truck above piles of scrap metal under a blue sky"></div>
<div class="abs brand"><div class="brand-dot"></div><div class="brand-name">BRAVOLY</div></div>

<svg class="abs" style="left:700px;top:28px" width="22" height="16" viewBox="0 0 22 16"><rect x="1" y="1" width="20" height="14" fill="none" stroke="#fff" stroke-width="1.6"/><path d="M1 1l10 8 10-8" fill="none" stroke="#fff" stroke-width="1.6"/></svg>
<div class="abs sep" style="left:738px"></div>
<div class="abs contact-top" style="left:752px"><small>E MAIL US</small>info@bravoly.com</div>
<svg class="abs" style="left:903px;top:26px" width="26" height="26" viewBox="0 0 24 24"><path d="M5 3h4l2 5-2.5 1.5a11 11 0 0 0 6 6L16 13l5 2v4a2 2 0 0 1-2 2A17 17 0 0 1 3 5a2 2 0 0 1 2-2z" fill="none" stroke="#fff" stroke-width="1.6"/></svg>
<div class="abs sep" style="left:938px"></div>
<div class="abs contact-top" style="left:952px"><small>CALL US NOW</small><span class="phone">555.014.2290</span></div>

<nav class="abs nav"><span class="active">HOME</span><span>ABOUT US</span><span>SERVICES</span><span>VEHICLES</span><span>PARTS</span><span>FAQ</span><span>CONTACT US</span></nav>
<div class="abs hero-title">AUTO RECYCLING</div>
<div class="abs hero-sub">Zeo waste, Zero Pollution, Zero hassles</div>
<div class="abs btn hero-btn">READ MORE</div>

<!-- Process -->
<div class="abs process-title"><div class="heading">OUR PROCESS</div><div class="rule"></div></div>

<div class="abs step" style="left:96px">
  <div class="icon">
    <svg width="80" height="56" viewBox="0 0 80 56"><path d="M16 24l7-15h34l7 15h6v20h-6v8h-10v-8H26v8H16v-8h-6V24z" fill="var(--green)"/><rect x="24" y="13" width="32" height="10" fill="#fff"/><circle cx="20" cy="33" r="4" fill="#fff"/><circle cx="60" cy="33" r="4" fill="#fff"/></svg>
    <div class="line"></div>
  </div>
  <h3>Getting to know your car</h3>
  <p>Lorem ipsum dolor sit ame consectetur adipiscing elit, sed do eiusmod tempor incididunt ut labore et dolore magna aliqua. Ut enim ad minim veniam quis nostrud exercitation</p>
</div>
<div class="abs step" style="left:440px">
  <div class="icon">
    <svg width="80" height="72" viewBox="0 0 80 72"><circle cx="42" cy="14" r="12" fill="var(--green)"/><text x="42" y="20" text-anchor="middle" font-family="Poppins,sans-serif" font-weight="700" font-size="16" fill="#fff">$</text><path d="M12 44h18l10 4h14l14-8 4 4-16 14H30l-6 10-12-6z" fill="var(--green)"/></svg>
  </div>
  <h3>We make on offer, instantly</h3>
  <p>Sed ut perspiciatis unde omnis iste natus error sit voluptatem accusantium doloremque laudantium, totam rem aperiam, eaque ipsa quae ab illo inventore veritatis et quasi .</p>
</div>
<div class="abs step" style="left:782px">
  <div class="icon">
    <svg width="80" height="60" viewBox="0 0 80 60"><circle cx="36" cy="32" r="24" fill="var(--green)"/><path d="M12 32h48M36 8v48M20 16c10 8 22 8 32 0M20 48c10-8 22-8 32 0" stroke="#fff" stroke-width="2" fill="none"/><path d="M56 2a9 9 0 0 1 9 9c0 7-9 16-9 16s-9-9-9-16a9 9 0 0 1 9-9z" fill="var(--green)" stroke="#fff" stroke-width="2"/><circle cx="56" cy="11" r="3" fill="#fff"/></svg>
  </div>
  <h3>Tell us when and where</h3>
  <p>On the other hand, we denounce with righteous indignation and dislike men who are so beguiled and demoralized by the charms of pleasure of the moment</p>
</div>

<!-- Why -->
<div class="abs why" role="img" aria-label="Green band over a faint scrapyard scene"></div>
<div class="abs why-mark">BRAVOLY</div>
<div class="abs why-divider"></div>
<div class="abs why-title">WHY BRAVOLY</div>
<ul class="abs why-list" style="left:519px">
  <li><svg width="12" height="10" viewBox="0 0 12 10"><path d="M1 5l3.5 3.5L11 1" stroke="#fff" stroke-width="2" fill="none"/></svg>Locally Owned &amp; Operated</li>
  <li><svg width="12" height="10" viewBox="0 0 12 10"><path d="M1 5l3.5 3.5L11 1" stroke="#fff" stroke-width="2" fill="none"/></svg>30+ Years Experience</li>
  <li><svg width="12" height="10" viewBox="0 0 12 10"><path d="M1 5l3.5 3.5L11 1" stroke="#fff" stroke-width="2" fill="none"/></svg>Licensed and Insured</li>
  <li><svg width="12" height="10" viewBox="0 0 12 10"><path d="M1 5l3.5 3.5L11 1" stroke="#fff" stroke-width="2" fill="none"/></svg>Large Used Parts Inventory</li>
  <li><svg width="12" height="10" viewBox="0 0 12 10"><path d="M1 5l3.5 3.5L11 1" stroke="#fff" stroke-width="2" fill="none"/></svg>Prompt Car Removal</li>
</ul>
<ul class="abs why-list" style="left:832px">
  <li><svg width="12" height="10" viewBox="0 0 12 10"><path d="M1 5l3.5 3.5L11 1" stroke="#fff" stroke-width="2" fill="none"/></svg>FREE TOWING</li>
  <li><svg width="12" height="10" viewBox="0 0 12 10"><path d="M1 5l3.5 3.5L11 1" stroke="#fff" stroke-width="2" fill="none"/></svg>Same Day Service</li>
  <li><svg width="12" height="10" viewBox="0 0 12 10"><path d="M1 5l3.5 3.5L11 1" stroke="#fff" stroke-width="2" fill="none"/></svg>Quick Response</li>
  <li><svg width="12" height="10" viewBox="0 0 12 10"><path d="M1 5l3.5 3.5L11 1" stroke="#fff" stroke-width="2" fill="none"/></svg>NO hidden fees</li>
  <li><svg width="12" height="10" viewBox="0 0 12 10"><path d="M1 5l3.5 3.5L11 1" stroke="#fff" stroke-width="2" fill="none"/></svg>NO hassle paperwork</li>
</ul>
<div class="abs btn why-btn">READ MORE</div>

<!-- Services -->
<div class="abs services"></div>
<div class="abs services-title"><div class="heading">OUR SERVICES</div><div class="rule"></div></div>

<div class="abs card" style="left:130px">
  <svg width="70" height="66" viewBox="0 0 70 66"><path d="M35 4l12 20h-8l-4-7-9 15-7-4z" fill="var(--green)"/><path d="M6 44l10-17 7 4-5 9h10v8H10z" fill="var(--green)"/><path d="M64 44l-6 10H40v6l-10-10 10-10v6h14l-6-10 7-4z" fill="var(--green)"/></svg>
  <h3>MODERN AUTO RECYCLING</h3>
  <p>Lorem ipsum dolor sit ame consectetur adipiscing elit, sed do eiusmod tempor incididunt ut labore et dolore magna aliqua. Ut enim ad minim.</p>
  <div class="btn btn-sm">READ MORE</div>
</div>
<div class="abs card" style="left:451px">
  <svg width="70" height="66" viewBox="0 0 70 66"><path d="M10 30l8-20h34l8 20v24h-9v-7H19v7h-9z" fill="var(--green)"/><rect x="21" y="15" width="28" height="12" fill="#fff"/><circle cx="20" cy="38" r="4" fill="#fff"/><circle cx="50" cy="38" r="4" fill="#fff"/></svg>
  <h3>NEW &amp; USED PARTS</h3>
  <p>Lorem ipsum dolor sit ame consectetur adipiscing elit, sed do eiusmod tempor incididunt ut labore et dolore magna aliqua. Ut enim ad minim.</p>
  <div class="btn btn-sm">READ MORE</div>
</div>
<div class="abs card" style="left:771px">
  <svg width="70" height="66" viewBox="0 0 70 66"><path d="M24 6h22l5 10v14H19V16z" fill="var(--green)"/><rect x="27" y="10" width="16" height="6" fill="#fff"/><path d="M6 36h16l10 5h12l14-7 6 4-18 14H28l-6 10-16-8z" fill="var(--green)"/></svg>
  <h3>WE BUY CARS</h3>
  <p>Lorem ipsum dolor sit ame consectetur adipiscing elit, sed do eiusmod tempor incididunt ut labore et dolore magna aliqua. Ut enim ad minim.</p>
  <div class="btn btn-sm">READ MORE</div>
</div>

<!-- Testimonials -->
<div class="abs testimonials" role="img" aria-label="Faded photo of cars at a wrecking yard under a cloudy sky"></div>
<div class="abs t-title"><div class="heading" style="color:#fff">TESTIMONIALS</div><div class="rule"></div></div>
<div class="abs qmark" style="left:244px;top:2128px">“</div>
<div class="abs quote">On the other hand, we denounce with righteous indignation and dislike men who are so beguiled and demoralized by the charms of pleasure of the moment, so blinded by desire, that they cannot foresee the pain and trouble that are bound to ensue; and equal blame belongs to those who fail in their duty through weakness of will, which is the.</div>
<div class="abs qmark" style="left:830px;top:2268px">”</div>
<svg class="abs" style="left:438px;top:2366px" width="14" height="22" viewBox="0 0 14 22"><path d="M11 2L3 11l8 9" stroke="#fff" stroke-width="2.5" fill="none"/></svg>
<div class="abs avatar" role="img" aria-label="Customer portrait" style="left:495px;top:2348px;width:58px;height:58px"></div>
<div class="abs avatar" role="img" aria-label="Portrait of Marcus, featured customer" style="left:573px;top:2341px;width:72px;height:72px;background:#c7c1b8"></div>
<div class="abs avatar" role="img" aria-label="Customer portrait" style="left:666px;top:2348px;width:58px;height:58px"></div>
<svg class="abs" style="left:761px;top:2366px" width="14" height="22" viewBox="0 0 14 22"><path d="M3 2l8 9-8 9" stroke="#fff" stroke-width="2.5" fill="none"/></svg>
<div class="abs t-name">MARCUS</div>

<!-- Blog -->
<div class="abs blog-title"><div class="heading">LATEST BLOG</div><div class="rule"></div></div>
<div class="abs post" style="left:130px">
  <div class="photo" role="img" aria-label="Rows of scrapped cars in a salvage yard" style="background:linear-gradient(160deg,#6b6f74,#3e3b3a)"></div>
  <h4>At vero eos et accusam et iusto odio dignissi</h4>
  <p>Lorem ipsum dolor sit ame cons ectetur adipiscing elit, sed do eius mod tempor incididunt ut labore</p>
  <div class="btn">READ MORE</div>
</div>
<div class="abs post" style="left:368px">
  <div class="photo" role="img" aria-label="Crane claw lifting a red car against a blue sky" style="background:linear-gradient(180deg,#2f6fd0,#7d98c0 55%,#6b6560)"></div>
  <h4>At vero eos et accusam et iusto odio dignissi</h4>
  <p>Lorem ipsum dolor sit ame cons ectetur adipiscing elit, sed do eius mod tempor incididunt ut labore</p>
  <div class="btn">READ MORE</div>
</div>
<div class="abs post" style="left:607px">
  <div class="photo" role="img" aria-label="Stacked wrecked cars in a yard under blue sky" style="background:linear-gradient(180deg,#4c7fc9,#8a9bb0 45%,#55565a)"></div>
  <h4>At vero eos et accusam et iusto odio dignissi</h4>
  <p>Lorem ipsum dolor sit ame cons ectetur adipiscing elit, sed do eius mod tempor incididunt ut labore</p>
  <div class="btn">READ MORE</div>
</div>
<div class="abs post" style="left:845px">
  <div class="photo" role="img" aria-label="Close-up of rusty used engine parts" style="background:linear-gradient(160deg,#7a5a48,#4a3a33 60%,#2f2a29)"></div>
  <h4>At vero eos et accusam et iusto odio dignissi</h4>
  <p>Lorem ipsum dolor sit ame cons ectetur adipiscing elit, sed do eius mod tempor incididunt ut labore</p>
  <div class="btn">READ MORE</div>
</div>

<!-- Quality -->
<div class="abs quality"></div>
<div class="abs quality-photo" role="img" aria-label="Pile of crushed cars stacked high under a stormy sky"></div>
<div class="abs q-title">QUALITY USED AUTO PARTS</div>
<p class="abs q-text">On the other hand, we denounce with righteous indig nation and dislike men who are so beguiled and demo ralized by the charms of pleasure of the moment, so blinded by desire, that they cannot foresee the pain and trouble that are bound to ensue; and equal blame belongs to those who fail in their duty through.</p>
<div class="abs btn q-btn">READ MORE</div>

<!-- Call back -->
<div class="abs callback" role="img" aria-label="Faint photo of parked used cars"></div>
<div class="abs cb-title"><div class="heading">REQUEST A CALL BACK</div><div class="rule"></div></div>
<div class="abs form"></div>
<div class="abs field" style="left:320px;top:3676px;width:266px;height:38px">FIRST NAME</div>
<div class="abs field" style="left:607px;top:3676px;width:266px;height:38px">LAST NAME</div>
<div class="abs field" style="left:320px;top:3731px;width:266px;height:38px">E MAIL</div>
<div class="abs field" style="left:607px;top:3731px;width:266px;height:38px">PH NO</div>
<div class="abs field msg" style="left:320px;top:3787px;width:553px;height:112px">MESSAGE</div>
<div class="abs btn submit">SUBMIT</div>

<!-- Footer -->
<footer class="abs footer"></footer>
<div class="abs f-mark"></div>
<div class="abs f-name">BRAVOLY</div>

<div class="abs f-head" style="left:441px">MENU</div>
<ul class="abs f-menu"><li>HOME</li><li>ABOUT US</li><li>SERVICES</li><li>VEHICLES</li><li>PARTS</li><li>FAQ</li><li>CONTACT US</li></ul>

<div class="abs f-head" style="left:633px">CONTACT US</div>
<div class="abs f-row" style="left:633px;top:4162px">
  <span class="f-ico"><svg width="10" height="14" viewBox="0 0 10 14"><path d="M5 0a5 5 0 0 1 5 5c0 4-5 9-5 9S0 9 0 5a5 5 0 0 1 5-5z" fill="#6b7477"/><circle cx="5" cy="5" r="2" fill="#fff"/></svg></span>
  <span>P.O. Box 4120, Station B<br>Harbour Town, NL, A0A 1A0</span>
</div>
<div class="abs f-row" style="left:633px;top:4225px">
  <span class="f-ico"><svg width="12" height="12" viewBox="0 0 24 24"><path d="M5 3h4l2 5-2.5 1.5a11 11 0 0 0 6 6L16 13l5 2v4a2 2 0 0 1-2 2A17 17 0 0 1 3 5a2 2 0 0 1 2-2z" fill="#6b7477"/></svg></span>
  <span>Call Us<br>555.014.2290</span>
</div>
<div class="abs f-row" style="left:633px;top:4287px">
  <span class="f-ico"><svg width="12" height="9" viewBox="0 0 12 9"><rect width="12" height="9" fill="#6b7477"/><path d="M0 0l6 5 6-5" stroke="#fff" fill="none"/></svg></span>
  <span>E mail Us<br>info@bravoly.com</span>
</div>

<div class="abs f-head" style="left:940px">FOLLOW US</div>
<div class="abs f-row" style="left:940px;top:4162px"><span class="f-ico"></span><span>Like us on<br>OUR PAGE</span></div>
<div class="abs f-row" style="left:940px;top:4222px"><span class="f-ico"></span><span>Follow us on<br>OUR NEWS</span></div>
<div class="abs f-row" style="left:940px;top:4284px"><span class="f-ico"></span><span>Follow us on<br>OUR NETWORK</span></div>

<div class="abs copy">Copyright © 2020 All Rights Reserved</div>

</body>
</html>
```